Podiatry clinic requires a modern revamp and editing of existing website.

I would like a fresh new look and updated information for my current business website. An easy to navigate site with prominent address and phone number for call to action. We are a podiatry clinic that focuses on general and sports podiatry.
I would like 4 pages; including Home page, About Us, Services & Contact.
www.brambleridgepodiatry.net

Target Market(s)

Active working professionals.

Industry/Entity Type

Medical

Coding

Coded - Design and coding required

Number of Pages Required

4 page

Font styles to use
Sans Serif

Colors
6b449b

Requirements
Must have
• A modern look with logo and active images; clean and uncluttered. Visible phone number and address for call to action.
• 4 pages - Home, About Us, Services, Contact.
• Home page - update address & service logos.
• About Us - update of personal information.
• Services - Revamp of existing page.
• Contact page to include Google map, email & phone number.
Nice to have
• Ability to add content easily; eg. a blog or adding video onto Home page.
• Link to Linkly page.

```html
<!DOCTYPE html>
<html lang="en">
<head>
<meta charset="utf-8">
<title>Bramble Ridge Podiatry</title>
<link rel="stylesheet" href="https://fonts.googleapis.com/css2?family=Roboto:wght@400;500;700&family=Caveat:wght@400&family=Merriweather:wght@300;400&family=Ubuntu:wght@400;500&display=swap">
<style>
:root{
  --purple:#6b449b;
  --purple-light:#8b6bb9;
  --purple-mid:#7a55a8;
  --lilac-bg:#f3f0f7;
  --card-bg:#efebf4;
  --grey-bg:#f5f5f6;
  --text:#222;
  --muted:#555;
  --placeholder:#bdbdbd;
  --nav-active:#3aa3e3;
  --link-orange:#e8724a;
}
*{box-sizing:border-box;margin:0;padding:0}
html,body{width:1200px;height:2586px;overflow:hidden;background:#fff}
body{font-family:"Roboto",Arial,sans-serif;color:var(--text);position:relative}

/* header */
.site-header{height:86px;border-top:2px solid #ddd;display:flex;align-items:center;justify-content:center}
.brand{display:flex;align-items:center;gap:10px;font-family:"Roboto",sans-serif;font-weight:700;font-size:22px;color:var(--purple)}
.brand-mark{width:30px;height:30px;background:var(--purple)}

/* hero */
.hero{position:relative;height:562px;background:linear-gradient(180deg,#8a8f96 0%,#b9a57d 35%,#a07a3c 62%,#4e3b22 100%);color:#fff;text-align:center}
.main-nav{position:absolute;top:108px;left:0;right:0;display:flex;justify-content:center;gap:40px;font-weight:700;font-size:16px}
.main-nav a{color:#fff;text-decoration:none}
.main-nav a.active{color:var(--nav-active)}
.hero-title{position:absolute;top:240px;left:0;right:0;font-family:"Caveat",cursive;font-weight:400;font-size:82px;letter-spacing:3px}
.hero-sub{position:absolute;top:350px;left:0;right:0;font-size:23px;line-height:33px}
.hero-actions{position:absolute;top:445px;left:0;right:0;display:flex;justify-content:center;gap:60px}
.btn{display:inline-block;height:36px;line-height:34px;padding:0 14px;font-size:10px;font-weight:700;text-transform:uppercase;border:1px solid #fff;border-radius:2px;text-decoration:none}
.btn-light{background:#fff;color:var(--nav-active);width:80px}
.btn-ghost{color:#fff;width:108px}
.slider-dots{position:absolute;top:614px;left:0;right:0;display:flex;justify-content:center;gap:8px}
.slider-dots span{width:10px;height:10px;border-radius:50%;border:2px solid #fff}
.slider-dots span.on{background:#fff}

/* contact band */
.contact-band{display:flex;height:148px;font-family:"Merriweather",serif;font-size:24px;line-height:36px;color:#fff}
.contact-band .half{flex:1;padding:32px 0 0 33px}
.contact-band .left{background:var(--purple-light)}
.contact-band .right{background:var(--purple);padding-left:33px}
.contact-band span{color:#d4c6e8;font-weight:300}

/* shared headings */
.section-title{text-align:center;font-size:22px;font-weight:500;padding-top:30px}
.dotted{height:0;border-top:2px dotted var(--purple-light);margin:14px auto 0}

/* about */
.about{height:228px}
.about .dotted{width:1091px}
.about p{margin-top:56px;text-align:center;font-size:12.5px;line-height:20.5px;color:var(--muted)}

/* products */
.products{height:333px;background:var(--lilac-bg)}
.products .section-title{padding-top:26px}
.products .dotted{width:1119px}
.product-list{display:flex;justify-content:center;gap:44px;margin-top:40px}
.product{width:330px;text-align:center}
.product-icon{width:76px;height:76px;margin:0 auto;background:var(--purple);display:flex;align-items:center;justify-content:center}
.product h3{font-size:17px;font-weight:700;margin-top:22px}
.product p{font-size:12.5px;line-height:20px;color:var(--muted);margin-top:14px}

/* blog */
.blog{height:548px}
.blog .section-title{padding-top:14px}
.blog .dotted{width:1091px}
.posts{display:flex;justify-content:center;gap:28px;margin-top:56px}
.post{width:253px;height:352px;background:var(--card-bg)}
.post-image{height:187px;background:var(--placeholder);display:flex;align-items:center;justify-content:center;font-size:32px;color:#111}
.post-body{padding:14px 19px 0}
.post h4{font-size:17px;font-weight:700}
.post p{font-size:12.5px;line-height:19px;color:var(--muted);margin-top:8px;height:58px}
.post-meta{border-top:1px solid #d6d0de;margin-top:10px;padding-top:14px;display:flex;justify-content:space-between;font-size:11px;color:#555}
.post-meta span{display:flex;align-items:center;gap:4px}
.view-more{position:absolute;top:1857px;left:538px;width:109px;height:36px;background:var(--purple);color:#fff;font-size:11px;font-weight:700;text-transform:uppercase;line-height:36px;text-align:center;border-radius:2px;text-decoration:none}

/* partners */
.partners{height:178px;background:var(--grey-bg);display:flex;align-items:center;justify-content:space-around;padding:0 40px}
.partner{background:#c9c9cc}
.partner.a{width:230px;height:44px;border-radius:22px}
.partner.b{width:185px;height:44px;border-radius:6px}
.partner.c{width:250px;height:70px;border-radius:6px}
.partner.d{width:230px;height:58px}

/* footer */
.site-footer{height:437px;background:var(--purple);color:#fff;text-align:center;font-family:"Ubuntu",sans-serif}
.site-footer .brand{color:#fff;justify-content:center;padding-top:86px;font-size:20px}
.site-footer .brand-mark{background:#fff;width:26px;height:26px}
.footer-contact{display:flex;justify-content:center;gap:42px;margin-top:20px;font-size:14.5px;line-height:20px;text-align:left}
.footer-contact .addr{text-align:right}
.share-note{margin-top:26px;font-size:14.5px}
.social{display:flex;justify-content:center;gap:12px;margin-top:28px}
.social a{width:69px;height:69px;border:3px solid #fff;border-radius:16px;display:flex;align-items:center;justify-content:center;color:#fff;text-decoration:none;font-size:12px;font-weight:500}

/* bottom bar */
.bottom-bar{height:66px;display:flex;align-items:center;justify-content:space-between;padding:0 62px 0 64px;font-family:"Ubuntu",sans-serif;font-size:13px;color:#444}
.mini-social{display:flex;gap:18px}
.mini-social span{width:28px;height:28px;border-radius:50%}
.bottom-bar a{color:var(--link-orange);text-decoration:none}

.c1{background:#3b5998}.c2{background:#cb2027}.c3{background:#55acee}.c4{background:#dc4e41}.c5{background:#0077b5}.c6{background:#1ab7ea}
</style>
</head>
<body>

<header class="site-header">
  <div class="brand"><span class="brand-mark"></span>Bramble Ridge Podiatry</div>
</header>

<section class="hero" role="img" aria-label="Runner's legs in sports shoes striding across a grassy hilltop at sunrise">
  <nav class="main-nav">
    <a class="active" href="#">Home</a><a href="#">Pages</a><a href="#">Features</a><a href="#">Works</a><a href="#">Blog</a><a href="#">Shop</a><a href="#">Contact</a>
  </nav>
  <h1 class="hero-title">Our Life's Work</h1>
  <p class="hero-sub">We Put Our Hearts and Souls into Making Every Case.<br>We Undertake the Very Best It Can Possibly Be.</p>
  <div class="hero-actions">
    <a class="btn btn-light" href="#">About Us</a>
    <a class="btn btn-ghost" href="#">Go on surfing</a>
  </div>
  <div class="slider-dots"><span class="on"></span><span></span><span class="on"></span></div>
</section>

<section class="contact-band">
  <div class="half left">Address <span>Suite 208 / 155 Harrow Lane</span><br>City <span>Eastvale 3141</span></div>
  <div class="half right">Phone <span>1300 555 019</span><br>Email <span>info@brambleridgepodiatry.net</span></div>
</section>

<section class="about">
  <h2 class="section-title">Bramble Ridge Podiatry</h2>
  <div class="dotted"></div>
  <p>Bramble Ridge Podiatry is a Podiatry clinic in the heart of Eastvale CBD. We are located between Kent &amp; Wilmot Streets in the Harbourview Business Centre.<br>
  Our podiatrists are fully qualified health professionals who are able to diagnose, treat, manage or help to prevent all medical conditions that affect the feet and lower limb.<br>
  We provide General Podiatry Treatment and some Specialised Services in relation to various foot conditions, including Sports Injuries, Orthotic Therapy and Nail Surgery.</p>
</section>

<section class="products">
  <h2 class="section-title">Podiatry &amp; Footwear Wellness Products</h2>
  <div class="dotted"></div>
  <div class="product-list">
    <div class="product">
      <div class="product-icon"><svg width="44" height="50" viewBox="0 0 44 50" fill="#fff"><ellipse cx="13" cy="30" rx="8" ry="17"/><ellipse cx="31" cy="26" rx="8" ry="17"/></svg></div>
      <h3>Podiatry Treatments</h3>
      <p>Podiatrits are trained to diagnose and trate all medical conditions that affect the feet and lower limb. At Bramble Ridge Podiatry we provide teatment for general &amp; Sports Podiatry conditions and veriuous specialised treatments</p>
    </div>
    <div class="product">
      <div class="product-icon"><svg width="44" height="50" viewBox="0 0 44 50" fill="none" stroke="#fff" stroke-width="3"><path d="M26 4c8 0 10 8 6 18s-6 20-16 22c-8 2-12-6-6-12s8-8 8-16 2-12 8-12z"/></svg></div>
      <h3>Podiatry Products Footwear</h3>
      <p>At Bramble Ridge Podiatry we stock and recomment veriuus products and footwear that aid in maintaining optimal foot health</p>
    </div>
    <div class="product">
      <div class="product-icon"><svg width="46" height="46" viewBox="0 0 46 46" fill="none" stroke="#fff" stroke-width="2.5" stroke-linejoin="round"><polygon points="23,3 29,17 44,18 32,28 36,43 23,35 10,43 14,28 2,18 17,17"/></svg></div>
      <h3>Health Wellness Products</h3>
      <p>At Bramble Ridge Podiatry, we believe that maintaining a healthy &amp; active lifestyle is the best way to prevent or manage debiliting foot conditions. We like to promote a healthy diet &amp; nutrition proper hydration and skin care</p>
    </div>
  </div>
</section>

<section class="blog">
  <h2 class="section-title">Blog</h2>
  <div class="dotted"></div>
  <div class="posts">
    <article class="post">
      <div class="post-image">270x200</div>
      <div class="post-body">
        <h4>Ullamcorper Parturien</h4>
        <p>Morbi leo risus, porta ac consectur at eros. Maecenas sed diam eget risus varius blandit sit amet non.</p>
        <div class="post-meta"><span><svg width="11" height="11" viewBox="0 0 11 11" fill="#555"><rect x="0" y="2" width="11" height="9"/><rect x="1.5" y="4.5" width="8" height="5" fill="#efebf4"/></svg>28 October, 2020</span><span><svg width="12" height="10" viewBox="0 0 12 10" fill="#555"><path d="M1 1h10v6H5l-3 3V7H1z"/></svg>15</span></div>
      </div>
    </article>
    <article class="post">
      <div class="post-image">270x200</div>
      <div class="post-body">
        <h4>Excepteur Sint Occaecat</h4>
        <p>Lorem ipsum dolor sit amet, consectetur adipiscing elit, sed do eiusmod tempor incididunt ut lab.</p>
        <div class="post-meta"><span><svg width="11" height="11" viewBox="0 0 11 11" fill="#555"><rect x="0" y="2" width="11" height="9"/><rect x="1.5" y="4.5" width="8" height="5" fill="#efebf4"/></svg>27 October, 2020</span><span><svg width="12" height="10" viewBox="0 0 12 10" fill="#555"><path d="M1 1h10v6H5l-3 3V7H1z"/></svg>11</span></div>
      </div>
    </article>
    <article class="post">
      <div class="post-image">270x200</div>
      <div class="post-body">
        <h4>Neque Porro Quisquam</h4>
        <p>Sed ut perspiciatis unde omnis iste natus error sit voluptatem accusantium doloremque laudanti.</p>
        <div class="post-meta"><span><svg width="11" height="11" viewBox="0 0 11 11" fill="#555"><rect x="0" y="2" width="11" height="9"/><rect x="1.5" y="4.5" width="8" height="5" fill="#efebf4"/></svg>26 October, 2020</span><span><svg width="12" height="10" viewBox="0 0 12 10" fill="#555"><path d="M1 1h10v6H5l-3 3V7H1z"/></svg>10</span></div>
      </div>
    </article>
    <article class="post">
      <div class="post-image">270x200</div>
      <div class="post-body">
        <h4>Quis Autem Vel Eum</h4>
        <p>Nemo enim ipsam voluptatem quia voluptas sit aspernatur aut odit aut fugit, sed quia consetur.</p>
        <div class="post-meta"><span><svg width="11" height="11" viewBox="0 0 11 11" fill="#555"><rect x="0" y="2" width="11" height="9"/><rect x="1.5" y="4.5" width="8" height="5" fill="#efebf4"/></svg>25 October, 2020</span><span><svg width="12" height="10" viewBox="0 0 12 10" fill="#555"><path d="M1 1h10v6H5l-3 3V7H1z"/></svg>15</span></div>
      </div>
    </article>
  </div>
</section>
<a class="view-more" href="#">View More</a>

<section class="partners" aria-label="Partner associations">
  <div class="partner a"></div>
  <div class="partner b"></div>
  <div class="partner c"></div>
  <div class="partner d"></div>
</section>

<footer class="site-footer">
  <div class="brand"><span class="brand-mark"></span>Bramble Ridge Podiatry</div>
  <div class="footer-contact">
    <div class="addr">Suite 208 / 155 Harrow Lane<br>Eastvale 3141</div>
    <div>Phone: 1300 555 019<br>Email: info@brambleridgepodiatry.net</div>
  </div>
  <p class="share-note">Share this page with friends who need help in 2016, too.</p>
  <div class="social">
    <a class="c1" href="#">Linkly</a><a class="c2" href="#">Snapwall</a><a class="c3" href="#">Chirper</a><a class="c4" href="#">Circlo</a><a class="c5" href="#">Workly</a><a class="c6" href="#">Reelo</a>
  </div>
</footer>

<div class="bottom-bar">
  <div class="mini-social"><span class="c1"></span><span class="c2"></span><span class="c3"></span><span class="c4"></span><span class="c5"></span><span class="c6"></span></div>
  <div><a href="#">Bramble Ridge</a> © 2016 All Rights Reserved <a href="#">Terms of Use</a> and <a href="#">Privacy Policy</a></div>
</div>

</body>
</html>
```